Norrell Advisory WA Business Card

Create an interesting, eye catching and colourful two sided business card. We are a business consulting operation assisting SME's improve all areas of their business. We provide consulting services to assist SME's to create a culture of continuous improvement, making a positive difference in the business. Our tag line is Small changes, big rewards. We want to create a well recognised, innovative brand that can be continued throughout our website, social media and email correspondence.

Target Market(s)

Small to Medium Enterprise Business Owners

Industry/Entity Type

Business Consultant

Contact Information for Business Card

Name of Business: Norrell Advisory - Steady steps lasting gains
Derek Holloway Ph 0407385510 Megan Holloway Ph 0407913847
Email norrelladvisorywa@mailbox-example.com
Web address TBA
FaceBook page TBA

BACKSIDE OF CARD

Providing assistance with:

• Organisation & Efficiency
• Revenue generation & Marketing
• Financial Management
• Production quality & delivery
• Systems & Process documentation
• Exit Strategy

Font styles to use
Other font styles liked:
• Calibri

Colors

Designer to choose colors to be used in the design.

Requirements
Must have
• Calibri font

```html
<!DOCTYPE html>
<html lang="en">
<head>
<meta charset="utf-8">
<title>Norrell Advisory WA Business Card</title>
<link rel="stylesheet" href="https://fonts.googleapis.com/css2?family=Open+Sans:ital,wght@0,400;0,600;0,700;1,700&display=swap">
<style>
  :root {
    --page-bg: #d9d9d9;
    --card-front: #ffffff;
    --card-back-top: #262626;
    --card-back-bottom: #161616;
    --ink-dark: #555555;
    --ink-mid: #8a8a8a;
    --rule: #7a7a7a;
    --wordmark-light: #d8d8d8;
    --tagline-grey: #8f8f8f;
    --brand-blue: #2e9bd6;
  }
  * { box-sizing: border-box; margin: 0; padding: 0; }
  html, body {
    width: 1125px; height: 1200px; overflow: hidden;
    background: var(--page-bg);
    font-family: "Open Sans", Calibri, Arial, sans-serif;
  }
  .card {
    position: absolute; left: 171px; width: 826px; height: 471px;
  }
  .card-front { top: 106px; background: var(--card-front); }
  .card-back {
    top: 639px;
    background: linear-gradient(160deg, var(--card-back-top), var(--card-back-bottom));
  }

  /* front */
  .person { position: absolute; left: 65px; color: var(--ink-dark); }
  .person-name { font-size: 31px; font-weight: 700; line-height: 1; letter-spacing: 0.2px; }
  .person-phone { font-size: 24px; font-weight: 700; line-height: 1; margin-top: 5px; }
  .person-one { top: 68px; }
  .person-two { top: 143px; }

  .contact-list { position: absolute; left: 65px; top: 218px; list-style: none; }
  .contact-list li {
    display: flex; align-items: center; gap: 9px;
    font-size: 17px; color: var(--ink-dark); height: 25px;
  }
  .contact-icon { width: 17px; height: 17px; flex: none; }

  .brand-block {
    position: absolute; left: 505px; top: 75px; width: 250px;
    display: flex; flex-direction: column; align-items: center; gap: 18px;
  }
  .brand-square { width: 130px; height: 130px; background: var(--brand-blue); }
  .brand-name { font-size: 24px; font-weight: 700; color: var(--ink-dark); }

  .services { position: absolute; left: 52px; top: 323px; width: 714px; }
  .services-heading {
    display: flex; align-items: center; gap: 6px;
    font-size: 26px; font-weight: 700; font-style: italic; color: var(--ink-dark);
    line-height: 1;
  }
  .services-heading::before, .services-heading::after {
    content: ""; flex: 1; height: 1px; background: var(--rule);
  }
  .services-heading::before { flex: 0 0 184px; }
  .services-line {
    text-align: center; font-size: 18px; color: var(--ink-mid);
    line-height: 25px; white-space: nowrap;
  }
  .services-line:first-of-type { margin-top: 4px; }
  .sep { font-size: 14px; padding: 0 3px; color: var(--ink-dark); vertical-align: 1px; }
  .services-rule { height: 1px; background: var(--rule); margin-top: 10px; }

  /* back */
  .back-mark {
    position: absolute; left: 343px; top: 100px;
    width: 140px; height: 140px; background: var(--brand-blue);
  }
  .back-wordmark {
    position: absolute; left: 0; right: 0; top: 322px; text-align: center;
    font-size: 40px; font-weight: 700; color: var(--wordmark-light);
    letter-spacing: 0.5px; line-height: 1;
  }
  .back-tagline {
    position: absolute; left: 0; right: 0; top: 372px; text-align: center;
    font-size: 17px; font-weight: 600; color: var(--tagline-grey);
    letter-spacing: 5px; line-height: 1;
  }
</style>
</head>
<body>
  <section class="card card-front">
    <div class="person person-one">
      <div class="person-name">DEREK HOLLOWAY</div>
      <div class="person-phone">0407385510</div>
    </div>
    <div class="person person-two">
      <div class="person-name">MEGAN HOLLOWAY</div>
      <div class="person-phone">0407913847</div>
    </div>

    <ul class="contact-list">
      <li>
        <svg class="contact-icon" viewBox="0 0 17 17"><circle cx="8.5" cy="8.5" r="6.5" fill="none" stroke="#555" stroke-width="2"/></svg>
        norrelladvisorywa
      </li>
      <li>
        <svg class="contact-icon" viewBox="0 0 17 17"><rect x="1" y="3.5" width="15" height="10" fill="none" stroke="#555" stroke-width="1.5"/><path d="M1 3.5 L8.5 9.5 L16 3.5" fill="none" stroke="#555" stroke-width="1.5"/></svg>
        norrelladvisorywa@mailbox-example.com
      </li>
      <li>
        <svg class="contact-icon" viewBox="0 0 17 17"><circle cx="8.5" cy="8.5" r="7.5" fill="#555"/><path d="M1 8.5 H16 M8.5 1 C4.5 5 4.5 12 8.5 16 M8.5 1 C12.5 5 12.5 12 8.5 16" fill="none" stroke="#fff" stroke-width="1"/></svg>
        www.norrelladvisorywa-example.com
      </li>
    </ul>

    <div class="brand-block">
      <div class="brand-square"></div>
      <div class="brand-name">Norrell Advisory</div>
    </div>

    <div class="services">
      <h2 class="services-heading">Providing assistance with</h2>
      <p class="services-line">Organisation &amp; Efficiency<span class="sep">•</span>Revenue generation &amp; Marketing<span class="sep">•</span>Financial Management</p>
      <p class="services-line">Production quality &amp; delivery<span class="sep">•</span>Systems &amp; Process documentation<span class="sep">•</span>Exit Strategy</p>
      <div class="services-rule"></div>
    </div>
  </section>

  <section class="card card-back">
    <div class="back-mark"></div>
    <div class="back-wordmark">NORRELL ADVISORY</div>
    <div class="back-tagline">STEADY STEPS LASTING GAINS</div>
  </section>
</body>
</html>
```